Velora Medspa Home Page Design

I need a home page designed for a medical spa of which there are thousands in the US. Their primary purpose is to enhance personal beauty using non-surgical means, such as laser treatment and micro-needling. Since insurance typically doesn't cover such procedures, we are appealing to a mostly upscale end user, probably about 70% female.

Target Market(s)

Women 35-54

Industry/Entity Type

Medical cosmetics

Number of Pages Required

1 page

Font styles to use
Other font styles liked:
• I want very readable content, even by seniors. No grey copy, please. Black only.

Requirements
Must have
• This needs to be a photo-heavy design. Here's one example among hundreds to illustrate what other practices put forth to attract patients. https://www.plomavista.example/ Stock photos are fine, though I would prefer they obtained from PixFarrow since I have an account with them. Finally, for now, I'm looking for a static website, we'll do the coding ourselves. Thank you. r psare
Nice to have
• I would also like you tpo consider staggering the five areas with content and a photo on the home page where the dominant photos are not always on the left or right. I think that help provide somefluidity to the sit's overall appearance. And "smooth" is a key quality as, in mamy cases, that's what attracts patients, i.e., the promise of smoother looking skin. his style: four e
Should not have
• Nice, open layout, but not loose. The home page document I attached contains all home page content and everything you need for the navigation bar.

```html
<!DOCTYPE html>
<html lang="en">
<head>
<meta charset="utf-8">
<title>Velora Medspa – Injectables</title>
<link href="https://fonts.googleapis.com/css2?family=Cabin:wght@500;600;700&family=Josefin+Sans:wght@400;600;700&display=swap" rel="stylesheet">
<style>
:root{
  --purple:#9b4a72;
  --olive:#8a8a33;
  --beige:#f0eedb;
  --pink:#f3e3ea;
  --footer-pink:#f2e2ea;
  --ink:#111111;
  --white:#ffffff;
  --line:#d9d9d9;
}
*{box-sizing:border-box;margin:0;padding:0}
html,body{width:1200px;height:4231px;overflow:hidden;background:var(--white)}
body{position:relative;font-family:"Josefin Sans",Arial,sans-serif;color:var(--ink)}
.abs{position:absolute}
.brand-name{font-family:"Cabin",Arial,sans-serif;font-weight:700;color:var(--purple);letter-spacing:1px;white-space:nowrap}
.btn{position:absolute;display:flex;align-items:center;justify-content:center;background:var(--olive);color:var(--white);font-size:13px;letter-spacing:.5px;text-transform:uppercase;padding-top:2px}
.photo{position:absolute}

/* header */
.site-header{position:absolute;left:0;top:0;width:1200px;height:112px;background:var(--white);box-shadow:0 2px 6px rgba(0,0,0,.08);z-index:2}
.header-logo{left:112px;top:38px;font-size:34px}
.topbar{position:absolute;left:381px;top:0;width:819px;height:36px}
.topbar-item{position:absolute;top:0;height:36px;display:flex;align-items:center;gap:8px;color:var(--white);font-size:12.5px}
.topbar-phone{left:416px;font-size:18px;font-weight:700}
.main-nav{position:absolute;top:66px;left:382px;display:flex;font-size:11.5px;text-transform:uppercase;letter-spacing:.2px}
.main-nav span{position:absolute;white-space:nowrap}
.main-nav .active{color:var(--purple)}

/* hero */
.hero{position:absolute;left:0;top:112px;width:1200px;height:438px;background:linear-gradient(90deg,#eef0f1 0%,#d9dee1 40%,#b8c1c7 100%);overflow:hidden}
.hero-photo{left:558px;top:0;width:642px;height:438px;background:
  radial-gradient(ellipse 120px 200px at 180px 200px,rgba(228,196,178,.9),rgba(228,196,178,0)),
  radial-gradient(ellipse 120px 200px at 400px 200px,rgba(236,208,190,.9),rgba(236,208,190,0)),
  linear-gradient(90deg,#c9cfd3 0%,#ddd2cb 35%,#e3d5cb 65%,#95a3ab 100%)}
.hero-curve{position:absolute;left:0;top:0}
.hero-title{left:113px;top:100px;font-family:"Cabin",Arial,sans-serif;font-weight:700;font-size:50px;letter-spacing:.5px}
.hero-sub{left:113px;top:158px;font-family:"Cabin",Arial,sans-serif;font-weight:500;font-size:37px;line-height:46px}
.hero-btn{left:113px;top:266px;width:240px;height:52px;font-size:15px}
.scroll-down{position:absolute;left:570px;top:525px;width:60px;height:60px;border-radius:50%;background:var(--white);box-shadow:0 3px 10px rgba(0,0,0,.15);display:flex;align-items:center;justify-content:center;z-index:3}

/* intro */
.intro-panel{left:0;top:665px;width:430px;height:501px;background:var(--beige)}
.intro-frame{left:207px;top:704px;width:361px;height:391px;border:1px solid #555}
.intro-photo{left:169px;top:721px;width:384px;height:420px;background:
  radial-gradient(ellipse 140px 120px at 110px 300px,rgba(233,190,214,.85),rgba(233,190,214,0)),
  linear-gradient(160deg,#e9e4df 0%,#e0c4b2 45%,#d9b8a3 70%,#c9b19c 100%)}
.intro-copy{left:640px;top:704px;width:400px;font-size:12px;line-height:24.5px;letter-spacing:.4px}
.intro-copy p{margin-bottom:4px}
.intro-btn{left:640px;top:1123px;width:166px;height:34px;font-size:12.5px}

/* procedures */
.proc-band{left:284px;top:1248px;width:916px;height:197px;background:var(--pink)}
.proc-heading{left:414px;top:1323px;font-family:"Cabin",Arial,sans-serif;font-weight:600;font-size:39px;color:var(--olive)}
.proc-text{position:absolute;width:400px}
.proc-text h3{font-family:"Cabin",Arial,sans-serif;font-weight:500;font-size:23px;color:var(--purple);margin-bottom:14px}
.proc-text p{font-size:12px;line-height:24.5px;padding-left:3px}
.learn-more{display:inline-block;margin-top:9px;margin-left:3px;font-size:12.5px;color:var(--purple);text-transform:uppercase;padding-bottom:6px;border-bottom:2px solid var(--purple)}
.img-lips{left:161px;top:1502px;width:437px;height:284px;background:linear-gradient(90deg,#8f9ea7 0%,#8f9ea7 50%,#eccdbb 62%,#f1d7c7 100%)}
.img-man{left:602px;top:1817px;width:437px;height:284px;background:linear-gradient(120deg,#dfe3e8 0%,#bfa28c 40%,#e9ecf1 70%,#9aa6b8 100%)}
.img-injection{left:161px;top:2147px;width:437px;height:284px;background:linear-gradient(110deg,#3d7f92 0%,#7fa2a8 30%,#b98d78 60%,#4b3a33 100%)}
.img-before{left:602px;top:2476px;width:227px;height:284px;background:linear-gradient(120deg,#d9a79b 0%,#e7b8ad 50%,#c58b86 100%)}
.img-after{left:835px;top:2476px;width:204px;height:284px;background:linear-gradient(120deg,#e0b5a8 0%,#efc6ba 50%,#d89aa2 100%)}
.ba-label{position:absolute;top:2735px;font-size:12px;color:var(--ink)}
.img-facial{left:161px;top:2815px;width:437px;height:284px;background:linear-gradient(120deg,#e2e2e0 0%,#f2ede8 40%,#dcc2b2 65%,#eeeeec 100%)}

/* consultation */
.consult-photo{left:0;top:3185px;width:578px;height:522px;background:
  radial-gradient(ellipse 90px 160px at 70px 300px,rgba(150,150,146,.35),rgba(150,150,146,0)),
  linear-gradient(135deg,#ececea 0%,#dcdcda 50%,#e6e6e4 100%)}
.consult-heading{left:162px;top:3238px;font-family:"Cabin",Arial,sans-serif;font-weight:600;font-size:39px;line-height:48px;color:var(--olive)}
.field{position:absolute;left:162px;width:350px;height:34px;background:rgba(255,255,255,.85);border:1px solid #cfcfcf;font-size:13px;padding:11px 12px 0}
.submit-btn{left:161px;top:3608px;width:130px;height:35px;font-size:12.5px}
.consult-copy{left:630px;top:3310px;width:400px;font-size:12px;line-height:24px}
.consult-copy p{margin-bottom:12px}
.consult-btn{left:630px;top:3518px;width:174px;height:34px;font-size:12.5px}

/* info */
.info-divider{left:599px;top:3784px;width:1px;height:181px;background:var(--line)}
.info-col{position:absolute;text-align:center;font-size:13px;line-height:21.5px}
.info-logo{font-size:32px;margin-bottom:8px;line-height:40px}
.hours-heading{font-family:"Cabin",Arial,sans-serif;font-weight:600;font-size:39px;color:var(--olive);line-height:44px;margin-bottom:8px}

/* footer */
.site-footer{position:absolute;left:0;top:4019px;width:1200px;height:212px;background:var(--footer-pink)}
.footer-deco{left:40px;top:20px;width:140px;height:175px;border-radius:70px 70px 20px 20px;background:linear-gradient(180deg,rgba(155,74,114,.07),rgba(155,74,114,.03))}
.footer-logo{left:0;top:45px;width:1200px;text-align:center;font-size:36px}
.footer-links{left:0;top:128px;width:1200px;text-align:center;font-size:12.5px}
.footer-links span{padding:0 7px}
.footer-copy{left:0;top:166px;width:1200px;text-align:center;font-size:12.5px}
</style>
</head>
<body>

<header class="site-header">
  <div class="abs brand-name header-logo">Velora Medspa</div>
  <svg class="topbar" width="819" height="36" viewBox="0 0 819 36" aria-hidden="true">
    <polygon points="0,36 18,0 517,0 535,36" fill="#9b4a72"/>
    <polygon points="526,0 819,0 819,36 544,36" fill="#8a8a33"/>
  </svg>
  <div class="topbar-item topbar-phone">
    <svg width="18" height="18" viewBox="0 0 24 24" aria-hidden="true"><path d="M6.6 10.8a15.2 15.2 0 0 0 6.6 6.6l2.2-2.2c.3-.3.7-.4 1-.2 1.1.4 2.3.6 3.6.6.6 0 1 .4 1 1V20c0 .6-.4 1-1 1A17 17 0 0 1 3 4c0-.6.4-1 1-1h3.5c.6 0 1 .4 1 1 0 1.3.2 2.5.6 3.6.1.3 0 .7-.2 1z" fill="#fff"/></svg>
    860-XXX-XXXX
  </div>
  <div class="topbar-item" style="left:597px">
    <svg width="12" height="16" viewBox="0 0 12 16" aria-hidden="true"><path d="M6 0a6 6 0 0 0-6 6c0 4.5 6 10 6 10s6-5.5 6-10a6 6 0 0 0-6-6zm0 8.2A2.2 2.2 0 1 1 6 3.8a2.2 2.2 0 0 1 0 4.4z" fill="#fff"/></svg>
    Serving Central Connecticut &amp; Beyond
  </div>
  <div class="topbar-item" style="left:914px">
    <svg width="22" height="18" viewBox="0 0 22 18" aria-hidden="true"><path d="M8 1C4 1 1 3.4 1 6.4c0 1.6.9 3 2.3 4L2.5 13l3.2-1.6c.7.2 1.5.3 2.3.3 4 0 7-2.4 7-5.4S12 1 8 1z" fill="none" stroke="#fff" stroke-width="1.5"/><path d="M16.5 6.5c2.6.6 4.5 2.4 4.5 4.6 0 1.2-.6 2.3-1.6 3.1l.6 2.3-2.6-1.3c-.6.2-1.3.3-2 .3-1.9 0-3.6-.7-4.6-1.8" fill="none" stroke="#fff" stroke-width="1.5"/></svg>
    FREE CONSULTATION
  </div>
  <nav class="main-nav">
    <span style="left:0">About</span>
    <span class="active" style="left:60px">Injectables &#8964;</span>
    <span style="left:173px">Laser Treatments &#8964;</span>
    <span style="left:327px">Micro Needling</span>
    <span style="left:447px">Other Treatment Options &#8964;</span>
    <span style="left:650px">Contact</span>
  </nav>
</header>

<section class="hero">
  <div class="photo hero-photo" role="img" aria-label="Before and after portrait of a woman in a spa headband showing smoother skin"></div>
  <svg class="hero-curve" width="1200" height="438" viewBox="0 0 1200 438" aria-hidden="true">
    <path d="M0 348 Q600 528 1200 343 L1200 438 L0 438 Z" fill="#fff"/>
  </svg>
  <h1 class="abs hero-title">INJECTABLES</h1>
  <p class="abs hero-sub">For A More Youthful<br>Looking You</p>
  <div class="btn hero-btn">Free Consultation</div>
</section>
<div class="scroll-down">
  <svg width="26" height="14" viewBox="0 0 26 14" aria-hidden="true"><path d="M1 1l12 11L25 1" fill="none" stroke="#8a8a33" stroke-width="2"/></svg>
</div>

<section>
  <div class="abs intro-panel"></div>
  <div class="abs intro-frame"></div>
  <div class="photo intro-photo" role="img" aria-label="Woman receiving a filler injection near the nose from a gloved hand"></div>
  <div class="abs intro-copy">
    <p>With aging comes the gradual formation of fine lines, wrinkles, loss of volume, along with changes in skin texture and tone. At Velora Medical Spa, our goal is to help you age with grace and confidence. If you’re looking to correct these and other problem areas, Velora offers injectable fillers that can combat signs of aging in lips, the lower face, cheeks, and other problem areas for a smoother and more youthful appearance.</p>
    <p>We provide a variety of FDA-approved injectable treatments, including Serenox®, Lumaderm®, Contoura®, Purexin®, and Velvara®, all performed by our skilled medical team. Dermal fillers can be injected into multiple areas of the face to revitalize and smooth the skin, reduce the appearance of wrinkles, and restore volume.</p>
    <p>Schedule a consultation with our facial rejuvenation specialists today to determine which treatment can best achieve your desired result.</p>
  </div>
  <div class="btn intro-btn">Free Consultation</div>
</section>

<section>
  <div class="abs proc-band"></div>
  <h2 class="abs proc-heading">Injectables Procedures</h2>

  <div class="photo img-lips" role="img" aria-label="Close-up of a woman's smooth lips and chin"></div>
  <div class="proc-text" style="left:646px;top:1547px">
    <h3>Serenox</h3>
    <p>Lorem ipsum dolor sit amet, consectetur adipiscing elit, sed do eiusmod tempor incididunt ut labore et dolore magna aliqua. Ut enim ad minim veniam, quis nostrud exercitation</p>
    <span class="learn-more">Learn More</span>
  </div>

  <div class="proc-text" style="left:159px;top:1876px">
    <h3>Velvara</h3>
    <p>Lorem ipsum dolor sit amet, consectetur adipiscing elit, sed do eiusmod tempor incididunt ut labore et dolore magna aliqua. Ut enim ad minim veniam, quis nostrud exercitation</p>
    <span class="learn-more">Learn More</span>
  </div>
  <div class="photo img-man" role="img" aria-label="Smiling man in a treatment chair looking into a hand mirror"></div>

  <div class="photo img-injection" role="img" aria-label="Gloved hand giving an injection beside a woman's eye"></div>
  <div class="proc-text" style="left:645px;top:2208px">
    <h3>Lumaderm</h3>
    <p>Lorem ipsum dolor sit amet, consectetur adipiscing elit, sed do eiusmod tempor incididunt ut labore et dolore magna aliqua. Ut enim ad minim veniam, quis nostrud exercitation</p>
    <span class="learn-more">Learn More</span>
  </div>

  <div class="proc-text" style="left:157px;top:2536px">
    <h3>Contoura</h3>
    <p>Lorem ipsum dolor sit amet, consectetur adipiscing elit, sed do eiusmod tempor incididunt ut labore et dolore magna aliqua. Ut enim ad minim veniam, quis nostrud exercitation</p>
    <span class="learn-more">Learn More</span>
  </div>
  <div class="photo img-before" role="img" aria-label="Jawline and neck before treatment"></div>
  <div class="photo img-after" role="img" aria-label="Jawline and neck after treatment"></div>
  <span class="ba-label" style="left:612px">Before</span>
  <span class="ba-label" style="left:988px">After</span>

  <div class="photo img-facial" role="img" aria-label="Woman relaxing while a practitioner applies a facial treatment with a brush"></div>
  <div class="proc-text" style="left:645px;top:2876px">
    <h3>Purexin</h3>
    <p>Lorem ipsum dolor sit amet, consectetur adipiscing elit, sed do eiusmod tempor incididunt ut labore et dolore magna aliqua. Ut enim ad minim veniam, quis nostrud exercitation</p>
    <span class="learn-more">Learn More</span>
  </div>
</section>

<section>
  <div class="photo consult-photo" role="img" aria-label="Stacked spa stones and palm leaves on a pale stone background"></div>
  <h2 class="abs consult-heading">Schedule Your<br>Free Consultation</h2>
  <div class="field" style="top:3354px">First Name</div>
  <div class="field" style="top:3397px">Last Name</div>
  <div class="field" style="top:3440px">Email</div>
  <div class="field" style="top:3483px">Phone</div>
  <div class="field" style="top:3526px;height:62px">Comments/Questions</div>
  <div class="btn submit-btn">Submit Now</div>
  <div class="abs consult-copy">
    <p><strong>Why wonder</strong> if you’re a candidate for our services when you can so easily find out for yourself?</p>
    <p>Simply complete and submit this form and a member of our medical team will contact you to schedule your visit.</p>
    <p>We’ll listen to your concerns, answer your questions, and recommend the best strategy for improving how you look and feel about yourself. That’s the Velora way.</p>
  </div>
  <div class="btn consult-btn">Free Consultation</div>
</section>

<section>
  <div class="abs info-divider"></div>
  <div class="info-col" style="left:181px;top:3812px;width:400px">
    <div class="brand-name info-logo">Velora Medspa</div>
    <p>Address: 410 Maple Crest Road Newington CT 06100</p>
    <p>Phone: 860-555-0142</p>
    <p>Email: info@veloramedspa.example</p>
  </div>
  <div class="info-col" style="left:619px;top:3816px;width:400px">
    <h2 class="hours-heading">Opening Hours</h2>
    <p>Monday To Friday – 10:00 AM To 7:00 PM</p>
    <p>Saturday – 10:00 AM To 6:00 PM</p>
    <p>Sunday – 11:00 AM To 5:00 PM</p>
  </div>
</section>

<footer class="site-footer">
  <div class="abs footer-deco" role="img" aria-label="Faint decorative illustration of herbal spa compresses"></div>
  <div class="abs brand-name footer-logo">Velora Medspa</div>
  <div class="abs footer-links"><span>About</span>|<span>Injectables</span>|<span>Laser Treatments</span>|<span>Micro Needling</span>|<span>Other Treatments</span>|<span>Contact</span></div>
  <div class="abs footer-copy">© 2023 Velora Med Spa &nbsp;|&nbsp; All Rights Reserved.</div>
</footer>

</body>
</html>
```